High-End Print/Digital Ad for Unique Luxury Travel Company Required

Objective:
Design a compelling and visually striking advertisement that highlights our company’s unmatched luxury travel experiences. The ad should elevate our brand image, spark curiosity, and drive prospective clients to contact us.
Target Audience:
• Affluent individuals seeking extraordinary, tailor-made travel experiences
• Affluent, luxury, high-net-worth individuals looking for value, expertise, and white-glove service
• Professionals or retirees who appreciate unique, thoughtfully curated travel over mainstream tourism
Key Messages to Communicate:
• One-of-a-kind luxury travel: Once-in-a-lifetime experiences that are curated with creativity and meticulous attention to detail
• Exceptional service: White-glove, personalized planning from start to finish
• 38 years’ travel experience – expert knowledge of destinations, modes of travel, premium accommodations and well-established, meaningful industry connections.
• Highly trusted: Cruise line executives often say, “No one does what you do.”
Tone and Style:
• Elegant, luxurious, sophisticated
• Eye-catching, polished, and modern
• Professional but warm—conveys trust and credibility
• High-impact visuals (full-bleed imagery, custom graphics, or high-end photography)
Deliverables:
• One full-page print ad and digital ad
• Ready-to-print, high-resolution file + working file (PSD, AI, etc.)
Optional: Social media-optimized version or short motion-graphic variation (if designer offers it)
Inspiration & Visual Style Suggestions:
• Think Lumen Voyages, Harrow Pike Wanderer, Silver Quill, or Orvel Retreats ad styles
• Large, emotive imagery with elegant typography
• Clean layout that speaks luxury, clarity, and trust
Copy Direction (draft):
For those who’ve explored the world—and crave something beyond the ordinary.
Each journey is a masterfully curated experience, rich in detail, seamless in execution, and unforgettable in every way.
Founded in 1997, Tidewell Journeys is a unique travel company specializing in cruising, all-inclusive luxury properties, and tours world-wide for individuals, groups, and incentives.
We offer an exceptional range of services designed to ensure every journey is flawlessly executed and truly unforgettable.
Let us help you plan your next extraordinary adventure.
Note: You may refine the copy slightly based on layout or format needs.
Other Resources for References:
1. Website - www.tidewelljourneys-example.com

```html
<!DOCTYPE html>
<html lang="en">
<head>
<meta charset="utf-8">
<title>Tidewell Journeys — Full Page Ad</title>
<link rel="stylesheet" href="https://fonts.googleapis.com/css2?family=Fraunces:opsz,wght@9..144,700;9..144,800&family=Oswald:wght@600&family=Poppins:wght@300;600;700;800&family=Source+Sans+3:wght@300;400&display=swap">
<style>
  :root {
    --navy: #164a82;
    --navy-deep: #1d3f86;
    --orange: #f0901e;
    --amber: #c17a2a;
    --ink: #333a44;
    --white: #ffffff;
  }
  * { margin: 0; padding: 0; box-sizing: border-box; }
  html, body { width: 953px; height: 1200px; overflow: hidden; background: var(--white); }
  .ad {
    position: relative;
    width: 953px;
    height: 1200px;
    overflow: hidden;
    background: var(--white);
    font-family: "Poppins", sans-serif;
  }
  .headline {
    position: absolute;
    top: 38px;
    left: 0;
    width: 100%;
    text-align: center;
    font-family: "Fraunces", serif;
    font-weight: 800;
    letter-spacing: -1px;
    line-height: 1;
  }
  .headline-lead { display: block; color: var(--navy); font-size: 47px; }
  .headline-key { display: block; color: var(--orange); font-size: 70px; margin-top: 2px; }
  .subline {
    position: absolute;
    top: 176px;
    left: 142px;
    width: 653px;
    height: 44px;
    border-radius: 22px;
    background: var(--navy);
    color: var(--white);
    font-family: "Poppins", sans-serif;
    font-weight: 300;
    font-size: 26px;
    line-height: 44px;
    text-align: center;
    z-index: 2;
  }
  .hero-photo {
    position: absolute;
    top: 208px;
    left: 0;
    width: 953px;
    height: 636px;
    background:
      linear-gradient(180deg,
        #f4e1b6 0%, #f2c88e 10%, #d99a6a 20%, #b7865f 34%,
        #8f8a5a 46%, #b89aa8 60%, #cdb7c7 72%, #a8917a 82%, #e7b347 92%, #f0a93a 100%);
  }
  .cta-badge {
    position: absolute;
    left: 553px;
    top: 657px;
    width: 314px;
    height: 314px;
    border-radius: 50%;
    background: var(--white);
    border: 3px solid var(--navy-deep);
    text-align: center;
    z-index: 3;
  }
  .cta-lead {
    margin-top: 68px;
    font-family: "Poppins", sans-serif;
    font-weight: 300;
    font-size: 29px;
    line-height: 1.1;
    color: var(--navy);
  }
  .cta-plan {
    font-family: "Oswald", sans-serif;
    font-weight: 600;
    font-size: 43px;
    line-height: 1.05;
    color: var(--amber);
    margin-top: 2px;
  }
  .cta-adventure {
    font-family: "Poppins", sans-serif;
    font-weight: 700;
    font-size: 35px;
    line-height: 1.08;
    color: var(--navy);
  }
  .intro {
    position: absolute;
    left: 62px;
    top: 903px;
    width: 380px;
  }
  .intro-title {
    font-family: "Poppins", sans-serif;
    font-weight: 700;
    font-size: 17.5px;
    line-height: 23px;
    color: var(--navy);
    letter-spacing: -0.2px;
  }
  .intro-body {
    margin-top: 12px;
    font-family: "Source Sans 3", sans-serif;
    font-weight: 300;
    font-size: 14px;
    line-height: 19px;
    color: var(--ink);
    width: 330px;
  }
  .brand {
    position: absolute;
    left: 475px;
    top: 1017px;
    width: 430px;
    display: flex;
    align-items: center;
    justify-content: center;
    gap: 12px;
  }
  .brand-dot {
    width: 34px;
    height: 34px;
    border-radius: 50%;
    background: var(--navy);
  }
  .brand-name {
    font-family: "Source Sans 3", sans-serif;
    font-weight: 400;
    font-size: 34px;
    letter-spacing: 1px;
    color: var(--navy);
  }
  .services {
    position: absolute;
    left: 475px;
    top: 1081px;
    width: 430px;
    text-align: center;
    font-family: "Source Sans 3", sans-serif;
    font-weight: 300;
    font-size: 16px;
    line-height: 20.5px;
    color: var(--ink);
  }
  .footer-band {
    position: absolute;
    left: 0;
    bottom: 0;
    width: 953px;
    height: 62px;
  }
  .footer-url {
    position: absolute;
    left: 62px;
    top: 1157px;
    font-family: "Poppins", sans-serif;
    font-weight: 600;
    font-size: 14.5px;
    letter-spacing: 2.4px;
    color: var(--white);
  }
</style>
</head>
<body>
  <main class="ad">
    <h1 class="headline">
      <span class="headline-lead">For those who’ve</span>
      <span class="headline-key">explored the world</span>
    </h1>
    <p class="subline">and crave something beyond the ordinary</p>

    <div class="hero-photo" role="img" aria-label="Sunset view over a colourful Mediterranean city park with mosaic-roofed gatehouses, palm trees and visitors strolling a plaza"></div>

    <div class="cta-badge">
      <p class="cta-lead">Let us help you</p>
      <p class="cta-plan">PLAN YOUR NEXT</p>
      <p class="cta-adventure">Extraordinary<br>Adventure</p>
    </div>

    <section class="intro">
      <h2 class="intro-title">Each journey is a<br>masterfully curated experience,<br>rich in detail, seamless in execution,<br>and unforgettable in every way.</h2>
      <p class="intro-body">Founded in 1997, Tidewell Journeys is a unique travel company specializing in cruising, all-inclusive luxury properties, and tours world-wide for individuals, groups, and incentives.</p>
    </section>

    <div class="brand">
      <span class="brand-dot"></span>
      <span class="brand-name">TIDEWELL JOURNEYS</span>
    </div>

    <p class="services">We offer an exceptional range of services designed to ensure every journey is flawlessly executed and truly unforgettable.</p>

    <svg class="footer-band" viewBox="0 0 953 62" preserveAspectRatio="none" aria-hidden="true">
      <path d="M0 0 H362 C395 0 408 10 420 18 C432 26 438 24 446 24 H953 V62 H0 Z" fill="#164a82"/>
    </svg>
    <p class="footer-url">www.tidewelljourneys-example.com</p>
  </main>
</body>
</html>
```